So the ones in the picture are my original cards that I came up with. 😅however I kinda messed up on two things, I missed spelled my name it should be Marcello Vandora as well as the email should be Marcellov@brightlanecrews.com. I would like to clean this card up and also make it pop! Something that people would remember me by and that screams DEMOLITION. As well as a card that give you a feeling of loyalty and trust. I would also like to change and remove junk hauling and add full demolition to replace it. These cards worked for a little while but I cant make that my image while handing these out. I would also like to only put down that we are located in Cedar Ridge Valley, CA, 90417 instead of the address on the card. Also if we can have a line that states Licensed, Bonded, & Insured. With out License # 4837215

Target Market(s)

Contractors and Home owners

Industry/Entity Type

Construction specialist in Demolition

Contact Information for Business Card

R Wrecking Selective Demolition & Full Demolition Kitchens AD Preparation Bathrooms Sheds Interiors & Exteriors Demo Digging And Much More Marcello Vandora Owner our city state and zip

Font styles to use
Serif
Sans Serif
Decorative

Colors
0054AA
0677BA
7BADD7
CADEEF
E8F1F8
0094D4
00A9DD
6FCCEA
C7EBF8
E9F6FB

Requirements
Must have
• License# 4837215
Nice to have
• Trying to go with a blue and white color scheme
Should not have
• Building construction

```html
<!DOCTYPE html>
<html lang="en">
<head>
<meta charset="UTF-8">
<title>RK Wrecking — Business Card</title>
<link href="https://fonts.googleapis.com/css2?family=Open+Sans:wght@400;600;700;800&family=Oswald:wght@500&display=swap" rel="stylesheet">
<style>
  :root {
    --backdrop: #232325;
    --card: #28292d;
    --gloss: #1b1c1f;
    --gloss-soft: #202124;
    --blue: #0054aa;
    --white: #ffffff;
  }
  * { box-sizing: border-box; margin: 0; padding: 0; }
  html, body {
    width: 1200px; height: 780px; overflow: hidden;
    background: var(--backdrop);
    font-family: "Open Sans", Arial, sans-serif;
  }
  .canvas { position: relative; width: 1200px; height: 780px; }
  .card {
    position: absolute; top: 92px;
    width: 340px; height: 595px;
    border-radius: 22px;
    background: var(--card);
    box-shadow: 0 18px 40px rgba(0,0,0,.55);
    overflow: hidden;
  }
  .card--back { left: 200px; }
  .card--front { left: 660px; }

  /* Back side */
  .back-mark {
    position: absolute; left: 50%; top: 50%;
    transform: translate(-50%, -50%) rotate(-90deg);
    text-align: center; white-space: nowrap;
  }
  .back-mark__name {
    display: flex; align-items: center; gap: 18px;
    font-weight: 800; font-size: 62px; letter-spacing: 1px;
    color: var(--gloss);
    text-shadow: 0 1px 0 rgba(255,255,255,.04);
  }
  .back-mark__dot { width: 46px; height: 46px; border-radius: 50%; background: var(--gloss); }
  .back-mark__license {
    margin-top: 6px;
    font-weight: 700; font-size: 20px; letter-spacing: 3px;
    color: var(--gloss-soft);
  }

  /* Front side */
  .front-curves { position: absolute; inset: 0; }
  .brand {
    position: absolute; top: 40px; left: 0; right: 0;
    display: flex; flex-direction: column; align-items: center;
  }
  .brand__name {
    display: flex; align-items: center; gap: 9px;
    font-weight: 800; font-size: 31px; color: var(--white); letter-spacing: .5px;
  }
  .brand__dot { width: 16px; height: 16px; border-radius: 50%; background: var(--blue); }
  .brand__license {
    margin-top: 2px; font-weight: 700; font-size: 10px; letter-spacing: 1.5px; color: var(--white);
  }
  .brand__assurance {
    margin-top: 3px; font-weight: 600; font-size: 11px; letter-spacing: .5px; color: var(--white);
  }
  .contact {
    position: absolute; top: 150px; left: 0; right: 0;
    text-align: center; color: var(--white);
  }
  .contact__name { font-weight: 700; font-size: 27px; color: var(--blue); line-height: 1.1; }
  .contact__role { font-size: 14px; font-weight: 600; margin-top: 2px; }
  .icon-row { display: flex; justify-content: center; gap: 8px; margin: 8px 0 6px; }
  .icon {
    width: 22px; height: 22px; border-radius: 50%;
    background: var(--blue); display: flex; align-items: center; justify-content: center;
  }
  .icon svg { width: 13px; height: 13px; }
  .contact__line { font-size: 13px; line-height: 1.35; }
  .contact__place { font-size: 13.5px; line-height: 1.3; margin-top: 2px; }
  .services {
    position: absolute; top: 400px; left: 0; right: 0;
    text-align: center; color: var(--white);
  }
  .services__title { font-weight: 700; font-size: 25px; color: var(--blue); line-height: 1.1; }
  .services__tagline {
    font-family: "Oswald", "Arial Narrow", sans-serif; font-weight: 500;
    font-size: 11px; letter-spacing: -.2px; margin: 2px 0 6px; text-transform: uppercase;
  }
  .services__list { list-style: none; font-size: 13.5px; line-height: 1.35; }
</style>
</head>
<body>
<main class="canvas">

  <section class="card card--back" aria-label="Card back">
    <div class="back-mark">
      <div class="back-mark__name"><span class="back-mark__dot"></span>RK Wrecking</div>
      <div class="back-mark__license">LICENSE#4837215</div>
    </div>
  </section>

  <section class="card card--front" aria-label="Card front">
    <svg class="front-curves" viewBox="0 0 340 595" preserveAspectRatio="none" aria-hidden="true">
      <path d="M0 280 Q 120 400 340 300 L340 595 L0 595 Z" fill="#222327"/>
      <path d="M0 300 Q 150 420 340 330 L340 595 L0 595 Z" fill="#1b1c1f" opacity=".7"/>
      <path d="M0 360 Q 190 430 340 380 L340 595 L0 595 Z" fill="#26272b"/>
    </svg>

    <header class="brand">
      <div class="brand__name"><span class="brand__dot"></span>RK Wrecking</div>
      <div class="brand__license">LICENSE#4837215</div>
      <div class="brand__assurance">Licensed, Bonded, &amp; Insured</div>
    </header>

    <div class="contact">
      <h1 class="contact__name">Marcello Vandora</h1>
      <p class="contact__role">Owner our city state and zip</p>
      <div class="icon-row">
        <span class="icon"><svg viewBox="0 0 24 24" fill="#fff"><path d="M6.6 10.8a15 15 0 0 0 6.6 6.6l2.2-2.2c.3-.3.7-.4 1-.2 1.1.4 2.3.6 3.6.6.6 0 1 .4 1 1V20c0 .6-.4 1-1 1A17 17 0 0 1 3 4c0-.6.4-1 1-1h3.5c.6 0 1 .4 1 1 0 1.3.2 2.5.6 3.6.1.3 0 .7-.2 1z"/></svg></span>
        <span class="icon"><svg viewBox="0 0 24 24" fill="none" stroke="#fff" stroke-width="2"><rect x="3" y="6" width="18" height="13" rx="1.5"/><path d="M3 7l9 6 9-6"/></svg></span>
        <span class="icon"><svg viewBox="0 0 24 24" fill="none" stroke="#fff" stroke-width="1.8"><circle cx="12" cy="12" r="9"/><path d="M3 12h18M12 3c3 3 3 15 0 18M12 3c-3 3-3 15 0 18"/></svg></span>
      </div>
      <p class="contact__line">(555) 014-7382</p>
      <p class="contact__line">info@brightlanecrews.com</p>
      <p class="contact__line">Marcellov@brightlanecrews.com</p>
      <div class="icon-row">
        <span class="icon"><svg viewBox="0 0 24 24" fill="none" stroke="#fff" stroke-width="2"><path d="M12 21s-6-6.2-6-11a6 6 0 0 1 12 0c0 4.8-6 11-6 11z"/><circle cx="12" cy="10" r="2.2"/></svg></span>
      </div>
      <p class="contact__place">Cedar Ridge Valley,<br>CA, 90417</p>
    </div>

    <div class="services">
      <h2 class="services__title">R Wrecking</h2>
      <p class="services__tagline">R Wrecking Selective Demolition &amp; Full Demolition</p>
      <ul class="services__list">
        <li>Sheds</li>
        <li>Digging</li>
        <li>Kitchens</li>
        <li>Bathrooms</li>
        <li>AD Preparation</li>
        <li>Interiors &amp; Exteriors Demo</li>
      </ul>
    </div>
  </section>

</main>
</body>
</html>
```